Building company buisness cards

We are looking for a sharp modern new look for our business cards.We are a New Zealand based company that specialises in house and land packages.We have attached a photo of the current logo and would like to see if it can be improved somehow if needed.We are open to any colours but we have chosen Black and White at this stage. Feel free to change the font and make the logo smarter looking.Play with the colours and see what looks best.We want a card that looks so good know one will want to throw it away!

Target Market(s)

Building profesonals, home buyers

Industry/Entity Type

Building

Contact Information for Business Card

Garrick Tenwood
0275390628
garrickt@hartvale.co.nz

Font styles to use
Serif
Sans Serif

Colors

Designer to choose colors to be used in the design.

Requirements
Must have
• Just the logo on one side and details on the other
• Clean simple looking card
Nice to have
• Round corners and detail like raised or spot UV
• Something that stands out
Should not have
• To title needed, Director etc

```html
<!DOCTYPE html>
<html lang="en">
<head>
<meta charset="utf-8">
<title>Hartvale business card</title>
<link rel="stylesheet" href="https://fonts.googleapis.com/css2?family=Playfair+Display:wght@700&family=Roboto:wght@400&display=swap">
<style>
  :root {
    --backdrop: #e4e4e4;
    --card-white: #ffffff;
    --ink: #0b0b0d;
    --text-grey: #444446;
    --back-dark: #0c0c0f;
    --back-mid: #1b1b1f;
    --mark-line: #ffffff;
  }
  * { box-sizing: border-box; margin: 0; padding: 0; }
  html, body {
    width: 1125px; height: 1200px; overflow: hidden;
    background: var(--backdrop);
  }
  .canvas { position: relative; width: 1125px; height: 1200px; }
  .card {
    position: absolute; left: 171px; width: 826px; height: 470px;
    border-radius: 22px; overflow: hidden;
  }
  .card-front { top: 106px; background: var(--card-white); }
  .card-back { top: 639px; }

  .holder-name {
    position: absolute; right: 43px; top: 61px;
    font-family: "Playfair Display", serif; font-weight: 700;
    font-size: 26px; letter-spacing: 0.3px; color: var(--ink);
    text-transform: uppercase; line-height: 1; white-space: nowrap;
  }
  .edge-tab {
    position: absolute; right: -22px; top: 52px;
    width: 44px; height: 44px; border-radius: 50%; background: var(--ink);
  }
  .wordmark {
    position: absolute; left: 54px; top: 172px;
    display: flex; align-items: center; gap: 18px;
  }
  .wordmark-name {
    font-family: "Playfair Display", serif; font-weight: 700;
    font-size: 88px; line-height: 1; color: var(--ink); letter-spacing: -1px;
  }
  .wordmark-dot {
    width: 92px; height: 92px; border-radius: 50%;
    border: 3px solid var(--ink); margin-top: 10px;
  }
  .contact-list {
    position: absolute; left: 54px; top: 348px; list-style: none;
    font-family: "Roboto", sans-serif; font-size: 19px; color: var(--text-grey);
  }
  .contact-list li { display: flex; align-items: center; height: 27px; }
  .contact-list svg { width: 18px; height: 18px; margin-right: 13px; fill: var(--ink); }

  .back-field {
    position: absolute; inset: 0;
    background: linear-gradient(160deg, var(--back-dark) 0%, var(--back-mid) 60%, var(--back-dark) 100%);
  }
  .back-dot {
    position: absolute; right: 58px; bottom: 42px;
    width: 66px; height: 66px; border-radius: 50%;
    border: 2.5px solid var(--mark-line);
  }
</style>
</head>
<body>
<main class="canvas">
  <section class="card card-front" aria-label="Card front">
    <span class="edge-tab"></span>
    <p class="holder-name">Garrick Tenwood</p>
    <div class="wordmark">
      <span class="wordmark-name">Hartvale</span>
      <span class="wordmark-dot"></span>
    </div>
    <ul class="contact-list">
      <li>
        <svg viewBox="0 0 24 24" aria-hidden="true"><path d="M6.6 10.8a15.1 15.1 0 0 0 6.6 6.6l2.2-2.2a1 1 0 0 1 1-.25 11.4 11.4 0 0 0 3.6.6 1 1 0 0 1 1 1V20a1 1 0 0 1-1 1A17 17 0 0 1 3 4a1 1 0 0 1 1-1h3.5a1 1 0 0 1 1 1c0 1.25.2 2.45.6 3.6a1 1 0 0 1-.25 1z"/></svg>
        0275390628
      </li>
      <li>
        <svg viewBox="0 0 24 24" aria-hidden="true"><path d="M2 6h20v12H2z M3 7l9 6 9-6" fill="none" stroke="#0b0b0d" stroke-width="2"/><path d="M2 6l10 7 10-7v12H2z"/></svg>
        garrickt@hartvale.co.nz
      </li>
      <li>
        <svg viewBox="0 0 24 24" aria-hidden="true"><circle cx="12" cy="12" r="10"/><path d="M7 7c2 0 3 1 3 3s-2 2-2 4 2 2 2 4M15 4c0 2 1 3 3 3M14 13c2 0 3 1 3 3" stroke="#fff" stroke-width="1.6" fill="none"/></svg>
        www.hartvale.co.nz
      </li>
    </ul>
  </section>

  <section class="card card-back" aria-label="Card back">
    <div class="back-field" role="img" aria-label="Dark background with a faint repeating brand pattern"></div>
    <span class="back-dot"></span>
  </section>
</main>
</body>
</html>
```